FOOD PROCESSING KICK ASS LANDING PAGE

My client is a food processing center in Massachusetts. They help startups process and scale up their products. Here is a write up: The Eastern Ridge Kitchen Works Hub was created in 2001 to support new and growing food businesses as they navigate the path of bringing a food product to market. Our mission is to promote economic development through entrepreneurship, provide opportunities for sustaining local agriculture, and promote best practices for food producers. The ERKWH offers rental manufacturing space as well as co-packing services to food businesses in the commonwealth and beyond. We also work with local farms to make value-added products, like jams, sauces, pickles and purees. In addition to these services, our team also provides one-on-one counseling and technical assistance, supporting you with business planning, product development, regulatory compliance and more. I made a mock up and video description. Please watch video: https://clipvuebox.net/watch/q7pLmZTqNeRw

General Inspiration:
Home page with banner photo: Co-Manufacturing - Brisbury Mill
https://www.pantrygrovemills.com/contact (contact page)
https://www.ovenlarkhub.org/
https://www.calloweybrook.com
https://www.hollistane.org/
https://www.spireladle.com/ (three key links on home page – kitchen, accelerator, on demand)
Business Services — Kettle Bay Hall: https://www.kettlebayhall.com/business-services

Here is the page we are redesigning and see list of vendors below: https://www.pwtgb.org/food-processing-center/

Only send landing page desktop view

Target Market(s)

Entrprenures

Industry/Entity Type

Food manufacturing

Number of Pages Required

1 page

Font styles to use
Sans Serif

Requirements
Must have
• Clean design that look amazing on mobile
Nice to have
• See mockup
Should not have
• See mockup

```html
<!DOCTYPE html>
<html lang="en">
<head>
<meta charset="utf-8">
<title>Eastern Ridge Kitchen Works Hub</title>
<link href="https://fonts.googleapis.com/css2?family=Outfit:wght@300;400;500;600;700&display=swap" rel="stylesheet">
<style>
:root{
  --orange:#d2612a;
  --dark:#333333;
  --peach:#fde9df;
  --teal:#4f7584;
  --teal-line:#7c9aa6;
  --ink:#222222;
  --green:#1f2b22;
  --footer:#f5f5f5;
  --white:#ffffff;
}
*{box-sizing:border-box;margin:0;padding:0}
html,body{width:1200px;height:4289px;overflow:hidden}
body{font-family:"Outfit",sans-serif;color:var(--ink);background:var(--white);position:relative}
section,header,footer{position:absolute;left:0;width:1200px}
.abs{position:absolute}
.photo{position:absolute}

/* header + hero */
.hero{top:0;height:676px;background:var(--white);overflow:hidden}
.hero-photo{left:0;top:0;width:1200px;height:676px;clip-path:polygon(757px 0,1200px 0,1200px 676px,483px 676px);background:linear-gradient(135deg,#d9d7d4 0%,#b9b4ad 35%,#e8e6e2 55%,#3e4153 80%,#2a2c38 100%)}
.topbar{top:0;left:700px;width:500px;height:74px;background:rgba(255,255,255,.55)}
.brand{left:125px;top:14px;display:flex;align-items:center;gap:10px}
.brand-dot{width:44px;height:44px;border-radius:50%;background:var(--orange)}
.brand-name{font-size:18px;font-weight:600;color:var(--orange);letter-spacing:.5px}
.nav{left:218px;top:30px;display:flex;gap:20px;font-size:11px;font-weight:500;text-transform:uppercase;color:var(--ink)}
.nav{left:280px}
.social{display:flex;gap:10px}
.social span{width:22px;height:22px;border-radius:50%;background:var(--orange);display:block}
.hero-social{left:927px;top:26px}
.hero-title{left:125px;top:128px;font-size:58px;line-height:68px;font-weight:700;color:var(--orange);letter-spacing:.5px}
.hero-lead{left:125px;top:338px;width:360px;font-size:19px;line-height:30px;font-weight:500;color:var(--ink)}
.btn{background:var(--orange);color:var(--white);border-radius:6px;font-weight:600;display:flex;align-items:center;justify-content:center;text-align:center}
.hero-btn{left:125px;top:529px;width:128px;height:37px;font-size:11px;gap:6px}
.hero-btn i{width:12px;height:12px;border:1.5px solid #fff;border-radius:50%;display:block}

/* prototype */
.prototype{top:676px;height:575px;background:var(--dark);color:var(--white)}
.h2{font-size:34px;font-weight:500}
.proto-title{left:125px;top:116px}
.proto-sub{left:125px;top:190px;width:330px;font-size:14px;line-height:23px;font-weight:600}
.small{font-size:11px;line-height:22px}
.proto-text{left:125px;top:258px;width:360px}
.proto-note{left:125px;top:372px;font-size:10.5px;font-weight:600}
.proto-btn{left:125px;top:406px;width:301px;height:53px;font-size:13px;line-height:17px}
.video{left:526px;top:94px;width:547px;height:385px;border-radius:6px;background:linear-gradient(160deg,#8f8f8d 0%,#6d6a66 40%,#4a4540 70%,#a78a66 100%)}
.play{left:244px;top:163px;width:60px;height:60px;border-radius:50%;background:rgba(0,0,0,.55)}

/* co-packing */
.copack{top:1251px;height:762px;background:var(--peach)}
.copack-photo{left:458px;top:0;width:742px;height:654px;background:linear-gradient(135deg,#4db340 0%,#b83a2e 30%,#e9d9b6 55%,#4db340 80%,#b83a2e 100%)}
.copack-box{left:125px;top:110px;width:692px;height:433px;background:var(--orange);color:var(--white);text-align:center}
.sec-title{display:inline-flex;align-items:center;gap:10px;font-size:34px;font-weight:500}
.sec-title::before{content:"";width:7px;height:32px;background:var(--teal);display:block}
.copack-box .sec-title{margin-top:30px}
.sub{font-size:14px;line-height:23px;font-weight:600;margin-top:10px}
.copack-box .body{text-align:left;width:496px;margin:28px auto 0}
.accordion{width:500px;margin:26px auto 0;background:var(--teal);text-align:left}
.accordion li{list-style:none;height:38px;padding:0 22px;display:flex;justify-content:space-between;align-items:center;font-size:13px;font-weight:600;color:var(--white);border-bottom:1px solid var(--teal-line)}
.accordion li:last-child{border-bottom:none}
.accordion li b{font-size:20px;font-weight:300}

/* value-added */
.value{top:2013px;height:763px;background:var(--peach)}
.value-photo{left:0;top:0;width:742px;height:763px;background:linear-gradient(150deg,#4a4e3e 0%,#7a3a22 30%,#d9a27c 50%,#3f4333 80%,#2f3328 100%)}
.value-box{left:508px;top:154px;width:692px;height:455px;background:var(--dark);color:var(--white);text-align:center}
.value-box .sec-title{margin-top:30px}
.value-box .body{text-align:left;width:484px;margin:22px auto 0}
.contact-line{font-size:10.5px;line-height:16px;font-weight:600;margin-top:22px}
.contact-line span{color:var(--orange);font-weight:400}
.value-box .accordion{width:492px;margin-top:18px}

/* about */
.about{top:2776px;height:527px;background:var(--peach)}
.about-title{left:125px;top:100px;color:var(--orange)}
.about-text{left:125px;top:172px;width:395px;color:#555}
.team-title{left:777px;top:122px;font-size:28px;font-weight:500}
.team{left:604px;top:174px;display:grid;grid-template-columns:repeat(3,150px);gap:12px 10px}
.member{background:var(--white);height:70px;border-radius:4px;padding:10px 20px}
.member h4{font-size:14px;font-weight:500}
.member p{font-size:9.5px;line-height:13px;color:#888;margin-top:3px}

/* entrepreneurs */
.makers{top:3303px;height:596px;background:radial-gradient(circle at 30% 40%,#2e3d2f 0%,#1b241c 60%,#141a15 100%);overflow:hidden}
.makers-title{left:125px;top:116px;color:var(--white);font-size:34px;font-weight:500}
.arrows{left:1018px;top:126px;display:flex;gap:22px}
.arrows svg{width:20px;height:24px}
.cards{left:125px;top:193px;display:flex;gap:10px}
.card{width:230px;height:290px;background:var(--white);border-radius:4px;overflow:hidden}
.card .img{height:228px}
.card h3{height:62px;display:flex;align-items:center;justify-content:center;font-size:22px;font-weight:500}

/* footer */
.site-footer{top:3899px;height:311px;background:var(--footer)}
.foot-brand{left:125px;top:70px;display:flex;align-items:center;gap:12px}
.foot-brand .brand-dot{width:70px;height:70px;background:#666}
.foot-brand .brand-name{font-size:26px;color:#444}
.foot-h{font-size:10px;font-weight:700;text-transform:uppercase;color:var(--ink)}
.foot-contact{left:404px;top:68px;width:300px}
.foot-contact ul{margin-top:20px;list-style:none}
.foot-contact li{display:flex;gap:12px;font-size:10px;line-height:15px;margin-bottom:8px;color:#333}
.foot-contact svg{width:12px;height:12px;flex:none}
.foot-social{margin-top:30px}
.foot-social span{width:20px;height:20px}
.newsletter{left:720px;top:68px;width:355px}
.newsletter p{font-size:10.5px;margin-top:20px;color:#333}
.field{height:32px;background:#666;border-radius:4px;color:#ccc;font-size:10px;display:flex;align-items:center;padding-left:18px}
.field.name{margin-top:8px;width:355px}
.row{display:flex;gap:6px;margin-top:12px}
.field.email{width:228px}
.subscribe{width:121px;height:32px;font-size:10px;border-radius:4px}
.cards-pay{display:flex;gap:6px;margin-top:20px}
.cards-pay span{width:34px;height:22px;border-radius:3px;background:#d8dce4;display:block}
.copyright{top:4210px;height:79px;background:var(--white)}
.copyright p{position:absolute;left:125px;top:36px;font-size:10px;color:#444}
</style>
</head>
<body>

<header class="hero">
  <div class="photo hero-photo" role="img" aria-label="Two staff members in masks and hairnets holding fresh blueberries over a processing bin"></div>
  <div class="abs topbar"></div>
  <div class="abs brand"><span class="brand-dot"></span><span class="brand-name">ERKWH</span></div>
  <nav class="abs nav"><span>Prototype</span><span>Co Packing</span><span>Value Add</span><span>About</span><span>Our Entrepreneurs</span></nav>
  <div class="abs social hero-social"><span></span><span></span><span></span><span></span><span></span></div>
  <h1 class="abs hero-title">EASTERN RIDGE<br>KITCHEN WORKS<br>HUB</h1>
  <p class="abs hero-lead">Promoting economic development through entrepreneurship, providing opportunities for sustaining local agriculture, and promoting best practices for food producers</p>
  <a class="abs btn hero-btn">Get In Touch <i></i></a>
</header>

<section class="prototype">
  <h2 class="abs h2 proto-title">Prototype My Food</h2>
  <p class="abs proto-sub">Are you an entrepreneur with a stellar recipe? Ready to commercial and scale?</p>
  <p class="abs small proto-text">Schedule a prototype with our team. We will work with you to turn your recipe into a commercial formula, select appropriate packaging, create a compliant label, and create a prototype of your product. Please submit an interest form to connect with our team.</p>
  <p class="abs proto-note">The ERKWH offers prototyping services from November-May.</p>
  <a class="abs btn proto-btn">Learn more about launching<br>a food business here</a>
  <div class="photo video" role="img" aria-label="Video still of two staff members waving beside boxes of product outdoors">
    <svg class="abs play" viewBox="0 0 60 60"><circle cx="30" cy="30" r="30" fill="rgba(0,0,0,.55)"/><path d="M24 18 L42 30 L24 42Z" fill="#fff"/></svg>
  </div>
</section>

<section class="copack">
  <div class="photo copack-photo" role="img" aria-label="Green bins of red apples beside labelled produce crates"></div>
  <div class="abs copack-box">
    <h2 class="sec-title">Co-Packing</h2>
    <p class="sub">Are you an established business<br>looking for co-packing support?<br><span style="font-weight:400">We can help!</span></p>
    <p class="small body">The ERKWH specializes in hot pack and hold processing for shelf-stable prepared and acidified foods. Additionally, we offer slow and individual-quick-freeze processing. If your food product doesn't fit into these categories, please give us a call to discuss. If it does, please submit an interest form to connect with our team.</p>
    <ul class="accordion">
      <li>What to expect<b>+</b></li>
      <li>Pricing<b>+</b></li>
      <li>Other qualifications and services<b>+</b></li>
    </ul>
  </div>
</section>

<section class="value">
  <div class="photo value-photo" role="img" aria-label="Hand holding up a jar of house-made pasta sauce outdoors"></div>
  <div class="abs value-box">
    <h2 class="sec-title">Value-Added</h2>
    <p class="sub">Turn your crops into value-added products!</p>
    <p class="small body">The Eastern Ridge Kitchen Works Hub can turn your crops into value added products. We offer 12 recipes for products that will feature your tomatoes, peppers, cukes, root veggies, apples and more! Farmers deliver the key ingredient(s) to Fairbrook and the ERKWH team will process, bottle, label and pack for you. We provide bottle, lid, label and case. Farmers sell finished product at their farm stands, as part of CSA's and in the wholesale market.</p>
    <p class="contact-line">Contact Tessa today to learn more<br><span>tessab@erkwh.org or 555-204-7180, ext. 104</span></p>
    <ul class="accordion">
      <li>Value-Added Products<b>+</b></li>
      <li>FAQ's<b>+</b></li>
      <li>Flash Freezing Options for Farms<b>+</b></li>
    </ul>
  </div>
</section>

<section class="about">
  <h2 class="abs h2 about-title">About Us</h2>
  <p class="abs small about-text">The Eastern Ridge Kitchen Works Hub was created in 2001 to support new and growing food businesses as they navigate the path of bringing a food product to market. Our mission is to promote economic development through entrepreneurship, provide opportunities for sustaining local agriculture, and promote best practices for food producers. The ERKWH offers rental manufacturing space as well as co-packing services to food businesses in the commonwealth and beyond. We also work with local farms to make value-added products, like jams, sauces, pickles and purees. In addition to these services, our team also provides one-on-one counseling and technical assistance, supporting you with business planning, product development, regulatory compliance, food safety and more.</p>
  <h2 class="abs team-title">Our Team</h2>
  <div class="abs team">
    <div class="member"><h4>Mara Kellen</h4><p>Director of Operations<br>555-204-7180 ext.110</p></div>
    <div class="member"><h4>Tessa Brandt</h4><p>Food Business Manager<br>555-204-7180 ext.104</p></div>
    <div class="member"><h4>Owen Larkin</h4><p>Floor Supervisor</p></div>
    <div class="member"><h4>Ivo Marquez</h4><p>Production Team Leader</p></div>
    <div class="member"><h4>Reed Callum</h4><p>Operations Team Leader</p></div>
    <div class="member"><h4>Paul Hennick</h4><p>Production Worker</p></div>
    <div class="member"><h4>Dario Velez</h4><p>Sanitation Specialist</p></div>
    <div class="member"><h4>Ben Ostrava</h4><p>Production Worker</p></div>
    <div class="member"><h4>Cruz Ramiro</h4><p>Production Worker</p></div>
  </div>
</section>

<section class="makers" role="region" aria-label="Meet our entrepreneurs">
  <h2 class="abs makers-title">Meet Our Entrepreneurs</h2>
  <div class="abs arrows">
    <svg viewBox="0 0 20 24"><path d="M14 3 L5 12 L14 21" fill="none" stroke="#d2612a" stroke-width="2.5"/></svg>
    <svg viewBox="0 0 20 24"><path d="M6 3 L15 12 L6 21" fill="none" stroke="#d2612a" stroke-width="2.5"/></svg>
  </div>
  <div class="abs cards">
    <div class="card"><div class="img" role="img" aria-label="Bottle of elderberry syrup with dried flowers" style="background:linear-gradient(135deg,#3b2f4a,#8a7e8e)"></div><h3>Quiet Meadow</h3></div>
    <div class="card"><div class="img" role="img" aria-label="Farm emblem over a field of strawberries" style="background:linear-gradient(135deg,#c8404a,#e8a0a0)"></div><h3>Birchline Farm</h3></div>
    <div class="card"><div class="img" role="img" aria-label="Jar of turmeric honey on a dark background" style="background:linear-gradient(135deg,#2a2a2a,#8a4d1d)"></div><h3>Hollow Oak Farm</h3></div>
    <div class="card"><div class="img" role="img" aria-label="Three bottles of maple syrup" style="background:linear-gradient(135deg,#f2efe9,#c26a2a)"></div><h3>Sapworth Foods</h3></div>
    <div class="card"><div class="img" role="img" aria-label="Jars of preserves on a shelf" style="background:linear-gradient(135deg,#7a3030,#c9b8a0)"></div><h3>Tenth Row</h3></div>
  </div>
</section>

<footer class="site-footer">
  <div class="abs foot-brand"><span class="brand-dot"></span><span class="brand-name">ERKWH</span></div>
  <div class="abs foot-contact">
    <h5 class="foot-h">Our Contact</h5>
    <ul>
      <li><svg viewBox="0 0 12 12"><path d="M2 1 L4.5 1 L5.5 3.5 L4 4.5 Q5 7 7.5 8 L8.5 6.5 L11 7.5 L11 10 Q5 11 1 3Z" fill="none" stroke="#d2612a"/></svg>555-204-7180</li>
      <li><svg viewBox="0 0 12 12"><path d="M6 11 Q2 6.5 2 4.5 A4 4 0 0 1 10 4.5 Q10 6.5 6 11Z" fill="none" stroke="#d2612a"/><circle cx="6" cy="4.5" r="1.4" fill="#d2612a"/></svg>88 Alder Lane, Fairbrook, MA 01990</li>
      <li><svg viewBox="0 0 12 12"><rect x="1" y="2.5" width="10" height="7" fill="none" stroke="#d2612a"/><path d="M1 2.5 L6 6.5 L11 2.5" fill="none" stroke="#d2612a"/></svg><span><b>Mara Kellen</b>, marak@erkwh.org<br><b>Tessa Brandt</b>, tessab@erkwh.org</span></li>
    </ul>
    <div class="social foot-social"><span></span><span></span><span></span><span></span><span></span></div>
  </div>
  <div class="abs newsletter">
    <h5 class="foot-h">Newsletter</h5>
    <p>Register here for our ERKWH Food Safety Newsletter:</p>
    <div class="field name">Full Name</div>
    <div class="row"><div class="field email">Email</div><a class="btn subscribe">Subscribe</a></div>
    <div class="cards-pay"><span></span><span></span><span></span><span></span><span></span></div>
  </div>
</footer>

<div class="copyright" style="position:absolute;left:0;width:1200px"><p>Copyright 2022 Eastern Ridge Kitchen Works Hub All rights reserved.</p></div>

</body>
</html>
```